Design website home page for pathology consulting company

Starting a new consulting company with anatomic pathologists focused on expert diagnosis and second opinions on difficult pathology cases. In the near future we will be incorporating next generation diagnostics for rare diseases of childhood into the business. These include discovery and testing of DNA for mutations.

The company is formed around one of the best known pathologists in the world named Marcel "Biscuit" Trowell. The name of the company is "BiscuitLab"

We had a logo design by SketchForum - it is great. I will attach file as soon as I have it (contest ending today). Our company is medical, uses microscopes, DNA, probably will focus on childhood diseases but not solely on childhood diseases. we're not particularly conservative, but the customers we want to appeal to include older practicing pathologists as well as patients (sometimes parents) looking for second opinions.

Think a group of expert doctors diagnosing disease through the microscope and through DNA technology, ages ranging from 35-75 all trained by the best pathologist in the world - "Biscuit"

We receive glass slides from diseases from patients all over the world from docs who need an expert to tell them what is the diagnosis. So "path to the diagnosis" is also part of the company marketing message.

We want the website design to describe our company but be very simple to find what one is looking for as we will use it as the launch page to:
1) order services
2) check results/reports
3) set up new account
4) speak with one of the pathologists
5) see our test menu
6) access our educational material/webinars
Updates

Update - looking for home page design and then finalists will ask for second page design to keep with theme - ok?

Reason: realized this project isn't web design but web home page design - thanks

Reason: Holidays for some in next two weeks

Reason: Hot discussion among collaborators for a few of the submissions. Will provide detail individually this weekend. Thanks so much for all the submissions!

Target Market(s)

Referring pathologists, physicians who want second opinions on pathology disease diagnosis, patients who have had biopsies (either patients themselves or parents of patients), generally high education level

Industry/Entity Type

Marketing

Requirements
Must have
• BiscuitLab
Next Generation Pathology Consultants

```html
<!DOCTYPE html>
<html lang="en">
<head>
<meta charset="utf-8">
<title>BiscuitLab — Next Generation Pathology Consultants</title>
<link rel="stylesheet" href="https://fonts.googleapis.com/css2?family=Open+Sans:ital,wght@0,300;0,400;0,600;0,700;1,400&family=Montserrat:wght@800&display=swap">
<style>
:root{
  --hero-dark:#1d2c48;
  --hero-mid:#2f4468;
  --brand-blue:#1f6db6;
  --band-blue:#2a78c8;
  --field-blue:#1565b8;
  --navy:#0e4f96;
  --sky:#2fa9e0;
  --cyan:#42c0e6;
  --grey-bg:#e4e4e4;
  --light-bg:#f6f6f6;
  --text:#333;
  --muted:#9a9a9a;
  --footer:#232323;
  --white:#fff;
}
*{box-sizing:border-box;margin:0;padding:0}
html,body{width:1200px;height:2456px;overflow:hidden}
body{position:relative;font-family:"Open Sans",Arial,sans-serif;color:var(--text);background:var(--grey-bg)}
.abs{position:absolute}

/* Hero */
.hero{position:absolute;left:0;top:0;width:1200px;height:740px;overflow:hidden}
.hero-photo{position:absolute;inset:0;background:radial-gradient(ellipse at 55% 45%,#3b5178 0%,var(--hero-mid) 35%,var(--hero-dark) 100%)}
.brand{left:111px;top:22px;display:flex;align-items:center;gap:12px}
.brand-dot{width:70px;height:70px;border-radius:50%;background:#8d97a6}
.brand-name{font-size:34px;font-weight:600;color:#3a8fd8;line-height:1}
.brand-tag{left:111px;top:130px;font-size:11px;color:#aab4c4}
.quick{top:26px;color:var(--white)}
.quick h4{font-size:16px;font-weight:400;margin-bottom:6px}
.quick p{font-size:12px;line-height:16px;width:135px}
.quick-divider{left:928px;top:26px;width:1px;height:56px;background:#8593ab}
.nav{top:106px;left:483px;display:flex;font-size:16px;color:var(--white)}
.nav a{color:inherit;text-decoration:none;position:absolute;top:0;line-height:30px;white-space:nowrap}
.nav .active{background:#8c9fb9;color:#1f5fa8;padding:0 15px;left:0}
.hero-rule{left:111px;top:165px;width:979px;height:1px;background:#4c5f80}
.hero-title{top:212px;width:1200px;text-align:center;font-size:36px;font-weight:300;color:var(--white);letter-spacing:.5px}
.feature{width:300px;text-align:center;color:var(--white)}
.feature .ring{width:168px;height:168px;margin:0 auto;border:3px solid var(--white);border-radius:50%;display:flex;align-items:center;justify-content:center}
.feature span{display:block;margin-top:10px;font-size:19px;font-weight:300;white-space:nowrap}
.btn-results{left:462px;top:625px;width:262px;height:51px;background:linear-gradient(#9a9a9a,#7d7d7d);border:1px solid #b5b5b5;border-radius:3px;color:var(--white);font-size:21px;font-weight:300;line-height:49px;text-align:center}

/* Speak band */
.speak{top:740px;left:0;width:1200px;height:157px;background:var(--band-blue)}
.speak h2{position:absolute;top:22px;width:1200px;text-align:center;font-size:26px;font-weight:400;color:var(--white)}
.field{top:77px;height:38px;background:var(--white);font-size:17px;color:#bbb;line-height:38px;padding-left:12px}
.field-icon{top:77px;width:40px;height:38px;background:var(--field-blue);display:flex;align-items:center;justify-content:center}
.btn-check{left:802px;top:77px;width:154px;height:38px;background:var(--field-blue);color:var(--white);font-size:19px;line-height:38px;text-align:center}

/* Pathologists */
.section-title{width:1200px;text-align:center;font-size:38px;font-weight:300;color:var(--brand-blue);line-height:1.2}
.card-photo{top:1053px;width:300px;height:208px}
.photo-a{background:linear-gradient(160deg,#a8b4bd,#6d93c0 60%,#8aa5c4)}
.photo-b{background:linear-gradient(160deg,#7e8f9f,#5d7fa6 55%,#a4b6c8)}
.card-title{top:1268px;font-size:20px;font-weight:400;color:var(--brand-blue)}
.card-text{top:1298px;width:304px;font-size:12px;line-height:24px;color:#444}
.btn-cond{top:1426px;width:180px;height:44px;background:var(--field-blue);border:2px solid #0a4f96;border-radius:3px;color:var(--white);font-size:17px;line-height:40px;text-align:center;white-space:nowrap}
.account{left:833px;top:1051px;width:257px;height:377px;background:#2a76c7;border-bottom:5px solid #1b2b44;border-radius:3px;overflow:hidden}
.account h3{position:absolute;top:16px;width:100%;text-align:center;font-size:19px;font-weight:400;color:var(--white)}
.acc-field{left:13px;width:228px;height:42px;background:var(--field-blue);color:var(--white);font-size:13px;line-height:42px;padding-left:42px}
.acc-field svg{position:absolute;left:12px;top:12px}
.btn-signup{left:46px;top:201px;width:164px;height:41px;background:var(--field-blue);color:var(--white);font-size:16px;line-height:41px;text-align:center}
.forgot{top:257px;width:100%;text-align:center;font-size:10px;color:var(--white)}
.social-signin{left:0;width:257px;height:43px;color:var(--white);font-size:12px;line-height:43px;text-align:center}

/* Education */
.education{top:1500px;left:0;width:1200px;height:340px;background:var(--light-bg)}
.edu-text{top:173px;left:135px;width:930px;text-align:center;font-size:15.5px;line-height:19px;color:var(--muted)}
.btn-read{left:527px;top:266px;width:179px;height:45px;background:var(--field-blue);border-radius:2px;color:var(--white);font-size:17px;line-height:45px;text-align:center}

/* Contact */
.form-label{left:111px;font-size:11px;font-style:italic;color:#555}
.form-input{left:111px;width:429px;height:35px;background:var(--white);border:1px solid #d6d6d6}
.btn-send{left:111px;top:2311px;width:67px;height:25px;background:var(--cyan);color:var(--white);font-size:12px;font-weight:700;line-height:25px;text-align:center}
.touch-title{left:610px;top:1922px;font-family:"Montserrat",Arial,sans-serif;font-weight:800;font-size:72px;letter-spacing:-5px;color:#0c0c0c;line-height:1;white-space:nowrap}
.touch-text{left:609px;top:2016px;width:470px;font-size:13.5px;line-height:25px;color:#222}
.social-box{top:2134px;width:33px;height:33px;background:#d4d4d4;border-radius:3px}
.contact-line{left:609px;font-size:14px;font-weight:700;color:#444;display:flex;align-items:center;gap:6px}

/* Footer */
.footer{left:0;top:2398px;width:1200px;height:58px;background:var(--footer)}
.footer p{position:absolute;left:110px;top:20px;font-size:12.5px;color:#ddd}
.footer-box{top:20px;width:18px;height:18px;background:#555;border-radius:2px}
</style>
</head>
<body>

<header class="hero">
  <div class="hero-photo" role="img" aria-label="Dimly lit operating room with surgical team, tinted deep blue"></div>
  <div class="abs brand"><span class="brand-dot"></span><span class="brand-name">BiscuitLab</span></div>
  <div class="abs brand-tag">Next Generation Pathology Consultants</div>

  <div class="abs quick" style="left:790px"><h4>See Test Menu</h4><p>Lorem ipsum dolor sit amet, consectetur</p></div>
  <div class="abs quick-divider"></div>
  <div class="abs quick" style="left:943px"><h4>Order Services</h4><p>Lorem ipsum dolor sit consectetur adipisicing</p></div>

  <nav class="abs nav">
    <a class="active">HOME</a>
    <a style="left:97px">ABOUT</a>
    <a style="left:182px">OUR PRACTICE</a>
    <a style="left:321px">NEWS/EVENTS</a>
    <a style="left:458px">BLOG</a>
    <a style="left:534px">CONTACT</a>
  </nav>
  <div class="abs hero-rule"></div>

  <h1 class="abs hero-title">OUR HEALTH CARE PROVIDER</h1>

  <div class="abs feature" style="left:84px;top:311px">
    <div class="ring">
      <svg width="90" height="90" viewBox="0 0 90 90" fill="none" stroke="#fff" stroke-width="6" stroke-linecap="round">
        <rect x="30" y="10" width="30" height="30" rx="4" fill="#fff" stroke="none"/>
        <path d="M45 16v18M36 25h18" stroke="#2f4468" stroke-width="5"/>
        <path d="M25 50v14a12 12 0 0 0 24 0v-6"/>
        <path d="M65 50v14a12 12 0 0 1-16 11"/>
        <circle cx="49" cy="54" r="5" fill="#fff"/>
      </svg>
    </div>
    <span>EXPERT DOCTORS</span>
  </div>

  <div class="abs feature" style="left:438px;top:311px">
    <div class="ring">
      <svg width="90" height="90" viewBox="0 0 90 90" fill="none" stroke="#fff" stroke-width="6" stroke-linejoin="round">
        <path d="M55 12l22 22-40 40a15 15 0 0 1-22-22z"/>
        <path d="M30 50l20 0-16 18a8 8 0 0 1-10-10z" fill="#fff" stroke="none"/>
        <path d="M50 8l32 32"/>
      </svg>
    </div>
    <span>PRACTICING PATHOLOGISTS</span>
  </div>

  <div class="abs feature" style="left:816px;top:311px">
    <div class="ring">
      <svg width="90" height="100" viewBox="0 0 90 100" fill="#fff">
        <path d="M30 38h16v16l18 34H12l18-34z"/>
        <rect x="56" y="34" width="9" height="42" transform="rotate(30 60 55)"/>
        <circle cx="38" cy="26" r="4"/><circle cx="32" cy="14" r="3"/><circle cx="44" cy="10" r="3.5"/><circle cx="40" cy="2" r="2"/>
      </svg>
    </div>
    <span>CHILDHOOD DISEASES</span>
  </div>

  <div class="abs btn-results">CHECK RESULT/REPORTS</div>
</header>

<section class="abs speak">
  <h2>SPEAK WITH ONE OF THE PATHOLOGIST</h2>
  <div class="abs field" style="left:236px;width:188px">name</div>
  <div class="abs field-icon" style="left:424px"><svg width="16" height="16" viewBox="0 0 16 16" fill="#fff"><circle cx="8" cy="5" r="4"/><path d="M0 16c0-5 4-7 8-7s8 2 8 7z"/></svg></div>
  <div class="abs field" style="left:475px;width:119px">email</div>
  <div class="abs field-icon" style="left:594px;color:#fff;font-size:18px;font-weight:700">@</div>
  <div class="abs field" style="left:643px;width:112px">date</div>
  <div class="abs field-icon" style="left:755px"><svg width="16" height="16" viewBox="0 0 16 16" fill="none" stroke="#fff" stroke-width="2"><rect x="2" y="3" width="12" height="11"/><path d="M2 7h12"/></svg></div>
  <div class="abs btn-check">CHECK NOW</div>
</section>

<h2 class="abs section-title" style="top:946px">PRACTICING PATHOLOGISTS</h2>

<div class="abs card-photo photo-a" style="left:111px" role="img" aria-label="Two smiling surgeons in scrubs and caps in an operating room"></div>
<h3 class="abs card-title" style="left:111px">Pathology Expert</h3>
<p class="abs card-text" style="left:111px">Lorem ipsum dolor sit amet, consectetur adipisicing elit, sed do eiusmod tempor incididunt ut labore et dolore magna aliqua. Ut enim ad minim veniam, quis nostrud exercitation ullamco laboris nisi ut aliquip ex ea commodo consequat.</p>
<div class="abs btn-cond" style="left:110px">Condition/Treatment</div>

<div class="abs card-photo photo-b" style="left:440px" role="img" aria-label="Surgeons in masks working under operating lights"></div>
<h3 class="abs card-title" style="left:440px">Dna Diseas Expertise</h3>
<p class="abs card-text" style="left:440px">Lorem ipsum dolor sit amet, consectetur adipisicing elit, sed do eiusmod tempor incididunt ut labore et dolore magna aliqua. Ut enim ad minim veniam, quis nostrud exercitation ullamco laboris nisi ut aliquip ex ea commodo consequat.</p>
<div class="abs btn-cond" style="left:438px">Condition/Treatment</div>

<aside class="abs account">
  <h3>Set Up New Account</h3>
  <div class="abs acc-field" style="top:74px"><svg width="20" height="16" viewBox="0 0 20 16" fill="none" stroke="#fff" stroke-width="2"><rect x="1" y="1" width="18" height="14"/><path d="M1 1l9 8 9-8"/></svg>janedoe@mailbox.net</div>
  <div class="abs acc-field" style="top:131px"><svg width="16" height="18" viewBox="0 0 16 18" fill="#fff"><rect x="1" y="8" width="14" height="10"/><path d="M4 8V5a4 4 0 0 1 8 0v3" fill="none" stroke="#fff" stroke-width="2"/></svg>Password</div>
  <div class="abs btn-signup">SIGN UP</div>
  <div class="abs forgot">Forgot Password?</div>
  <div class="abs social-signin" style="top:288px;background:var(--navy)">Sign in with Friendnet</div>
  <div class="abs social-signin" style="top:331px;background:var(--sky)">Sign in with Chirper</div>
</aside>

<section class="abs education">
  <h2 class="abs section-title" style="top:44px">ACCES OUR EDUCATION<br>MATERIAL</h2>
  <p class="abs edu-text">Big enough to offer state of the art treatment. Small enough to take the time for personalized spinal and cranial care for each of our patients. At Riverbend Neurosurgical Associates, each of our neurosurgeons is a fellowship trained specialist, yet we maintain a one on one relationship with each of our patients. We're proud to provide a unique blend of technical excellence combined with kind and compassionate care.</p>
  <div class="abs btn-read">READ MORE</div>
</section>

<label class="abs form-label" style="top:1921px">Your Name (required)</label>
<div class="abs form-input" style="top:1943px"></div>
<label class="abs form-label" style="top:1993px">Your Email (required)</label>
<div class="abs form-input" style="top:2015px"></div>
<label class="abs form-label" style="top:2065px">Subject</label>
<div class="abs form-input" style="top:2087px"></div>
<label class="abs form-label" style="top:2137px">Your Message</label>
<div class="abs form-input" style="top:2159px;height:139px"></div>
<div class="abs btn-send">Send</div>

<h2 class="abs touch-title">BE IN TOUCH</h2>
<p class="abs touch-text">Lorem ipsum dolor sit amet, consectetur adipiscing elit. Suspendisse pulvinar scelerisque dictum. Donec iaculis, diam sit amet suscipit feugiat, diam magna volutpat augue, sit amet varius nulla turpis sit amet lacus. Aenean faucibus, sem quis convallis lobortis.</p>

<div class="abs social-box" style="left:609px"></div>
<div class="abs social-box" style="left:653px"></div>
<div class="abs social-box" style="left:697px"></div>
<div class="abs social-box" style="left:741px"></div>
<div class="abs social-box" style="left:785px"></div>
<div class="abs social-box" style="left:829px"></div>
<div class="abs social-box" style="left:873px"></div>
<div class="abs social-box" style="left:917px"></div>
<div class="abs social-box" style="left:961px"></div>
<div class="abs social-box" style="left:1005px"></div>

<div class="abs contact-line" style="top:2208px"><svg width="13" height="12" viewBox="0 0 13 12" fill="#444"><path d="M6.5 0L13 6h-2v6H8V8H5v4H2V6H0z"/></svg>Cedar Hollow, CA 94100</div>
<div class="abs contact-line" style="top:2244px"><svg width="13" height="10" viewBox="0 0 13 10" fill="#444"><rect width="13" height="10"/><path d="M0 0l6.5 5L13 0" fill="none" stroke="#e4e4e4"/></svg>hello@biscuitlab-mail.com</div>
<div class="abs contact-line" style="top:2280px"><svg width="12" height="12" viewBox="0 0 12 12" fill="#444"><rect width="12" height="12" rx="2"/><path d="M3 2l2 2-1 1.5c.6 1.2 1.4 2 2.5 2.5L8 7l2 2-1.5 1.5C5 10 2 7 1.5 3.5z" fill="#e4e4e4"/></svg>(555) 014-2200</div>
<div class="abs contact-line" style="top:2316px"><svg width="12" height="12" viewBox="0 0 12 12" fill="none" stroke="#444" stroke-width="2"><path d="M5 7l3-3M4 5L2 7a2 2 0 0 0 3 3l2-2M8 7l2-2a2 2 0 0 0-3-3L5 4"/></svg>www.biscuitlab-mail.com</div>

<footer class="abs footer">
  <p>Copyright All Rights Reserved © 2012</p>
  <div class="abs footer-box" style="left:900px"></div>
  <div class="abs footer-box" style="left:924px"></div>
  <div class="abs footer-box" style="left:948px"></div>
  <div class="abs footer-box" style="left:972px"></div>
  <div class="abs footer-box" style="left:996px"></div>
  <div class="abs footer-box" style="left:1020px"></div>
  <div class="abs footer-box" style="left:1044px"></div>
  <div class="abs footer-box" style="left:1068px"></div>
</footer>

</body>
</html>
```